Cards
Hollowmere Estate Advisors
Project: Cards
Cards - Real Estate
Creative Brief
Modern
Teodoro Villanueva
Managing Broker
487 Quarry Ln. Brinmoor NQ 46390
homesbytv@brindlepost.net
I also need the Dwellcor/HXR logo, along with the Open Hearth logo

```html
<!DOCTYPE html>
<html lang="en">
<head>
<meta charset="utf-8">
<title>Hollowmere Estate Advisors – Business Card</title>
<link rel="stylesheet" href="https://fonts.googleapis.com/css2?family=Crimson+Pro:wght@400;600;700&display=swap">
<style>
  :root {
    --bg: #e6e6e6;
    --card: #ffffff;
    --ink: #2b2b2b;
    --green: #5c9a2c;
    --blue: #2b86c6;
    --rule: #9a9a9a;
    --badge: #3a3a3a;
  }
  * { box-sizing: border-box; margin: 0; padding: 0; }
  html, body { width: 1200px; height: 780px; overflow: hidden; }
  body {
    background: var(--bg);
    font-family: "Crimson Pro", Georgia, serif;
    color: var(--ink);
    position: relative;
  }
  .card {
    position: absolute;
    left: 75px; top: 90px;
    width: 1050px; height: 600px;
    background: var(--card);
    border-radius: 44px;
    box-shadow: 0 6px 24px rgba(0,0,0,.18);
  }
  .badges {
    position: absolute;
    top: 40px; right: 48px;
    display: flex; gap: 18px;
  }
  .badge {
    width: 62px; height: 62px;
    border: 4px solid var(--badge);
    border-radius: 4px;
  }
  .badge--wide { width: 120px; }
  .brand {
    position: absolute;
    left: 160px; top: 170px;
    display: flex; align-items: center; gap: 26px;
    color: var(--ink);
    font-weight: 600;
  }
  .brand-mark {
    width: 130px; height: 130px;
    background: var(--ink);
  }
  .brand-name { line-height: 1; }
  .brand-name .line1 { display: block; font-size: 64px; letter-spacing: 1px; text-transform: uppercase; }
  .brand-name .line2 { display: block; font-size: 30px; letter-spacing: 1px; text-transform: uppercase; margin-top: 4px; }
  .person {
    position: absolute;
    right: 580px; top: 345px;
    text-align: right;
  }
  .person-name { color: var(--green); font-weight: 700; font-size: 36px; white-space: nowrap; }
  .person-title { color: var(--blue); font-size: 27px; margin-top: 2px; }
  .person-address { font-size: 26px; line-height: 1.3; margin-top: 14px; }
  .divider {
    position: absolute;
    left: 495px; top: 350px;
    width: 2px; height: 175px;
    background: var(--rule);
  }
  .contacts {
    position: absolute;
    left: 515px; top: 346px;
    list-style: none;
    font-size: 27px;
  }
  .contacts li { display: flex; align-items: center; gap: 12px; height: 42px; white-space: nowrap; }
  .contacts svg { width: 24px; height: 24px; fill: var(--green); flex: none; }
</style>
</head>
<body>
  <main class="card">
    <div class="badges">
      <div class="badge badge--wide" aria-label="Dwellcor HXR badge"></div>
      <div class="badge" aria-label="Open Hearth badge"></div>
    </div>

    <div class="brand">
      <div class="brand-mark"></div>
      <div class="brand-name">
        <span class="line1">Hollowmere</span>
        <span class="line2">Estate Advisors</span>
      </div>
    </div>

    <section class="person">
      <h1 class="person-name">Teodoro Villanueva</h1>
      <p class="person-title">Managing Broker</p>
      <p class="person-address">487 Quarry Ln.<br>Brinmoor NQ 46390</p>
    </section>

    <div class="divider"></div>

    <ul class="contacts">
      <li>
        <svg viewBox="0 0 24 24"><path d="M6.6 10.8a15.1 15.1 0 0 0 6.6 6.6l2.2-2.2c.3-.3.7-.4 1-.2 1.1.4 2.3.6 3.6.6.6 0 1 .4 1 1V20c0 .6-.4 1-1 1A17 17 0 0 1 3 4c0-.6.4-1 1-1h3.5c.6 0 1 .4 1 1 0 1.3.2 2.5.6 3.6.1.3 0 .7-.2 1z"/></svg>
        <span>219-555-0147</span>
      </li>
      <li>
        <svg viewBox="0 0 24 24"><path d="M7 1h10a2 2 0 0 1 2 2v18a2 2 0 0 1-2 2H7a2 2 0 0 1-2-2V3a2 2 0 0 1 2-2zm0 3v14h10V4zm5 15.5a1.2 1.2 0 1 0 0 2.4 1.2 1.2 0 0 0 0-2.4z"/></svg>
        <span>219-555-0183</span>
      </li>
      <li>
        <svg viewBox="0 0 24 24"><path d="M6 2h9l3 3v4h1a3 3 0 0 1 3 3v7h-4v3H6v-3H2v-7a3 3 0 0 1 3-3h1zm2 2v5h8V6h-2V4zm0 12v4h8v-4z"/></svg>
        <span>219-555-0129</span>
      </li>
      <li>
        <svg viewBox="0 0 24 24"><path d="M2 5h20v14H2zm2 2v.5l8 5.5 8-5.5V7zm0 3v7h16v-7l-8 5.5z"/></svg>
        <span>homesbytv@brindlepost.net</span>
      </li>
    </ul>
  </main>
</body>
</html>
```